Larkfield Ridge Management

I need a professional website. My current website is larkfieldridgemanagement.com and I hate it. It was created with some AI tool very quickly because I needed a site up and running with no advanced notice. I’m open to all designs .. I trust you, the professionals will deliver the results I’m anxiously awaiting! :)

```html
<!DOCTYPE html>
<html lang="en">
<head>
<meta charset="utf-8">
<title>Larkfield Ridge Management</title>
<link rel="stylesheet" href="https://fonts.googleapis.com/css2?family=Inter:wght@400;500;600;700&display=swap">
<style>
:root{
  --navy:#1f3461;
  --navy-dark:#1b2c52;
  --red:#a3141f;
  --pink:#f8e4e4;
  --ink:#3a3a3a;
  --grey-bg:#f4f4f4;
  --contact-bg:#9b9b9b;
  --white:#ffffff;
}
*{box-sizing:border-box;margin:0;padding:0}
html,body{width:1200px;height:3868px;overflow:hidden}
body{position:relative;font-family:'Inter',sans-serif;color:var(--ink);background:var(--white)}
.abs{position:absolute}
.btn{position:absolute;display:flex;align-items:center;justify-content:center;background:var(--red);color:var(--white);font-weight:700;font-size:15px;letter-spacing:.2px}
.btn.soft{background:var(--pink);color:var(--red)}
.heading{position:absolute;font-weight:600;font-size:41px;color:var(--navy);letter-spacing:-.5px}
.heading::after{content:"";position:absolute;left:50%;transform:translateX(-50%);bottom:-9px;width:76px;height:3px;background:var(--red)}
.heading.left::after{left:0;transform:none}
/* header */
.nav a{position:absolute;top:48px;font-size:14.5px;font-weight:600;color:#222;text-decoration:none}
.nav a.active{color:var(--red);border-bottom:2px solid var(--red);padding-bottom:2px}
.social-sq{position:absolute;top:41px;width:32px;height:32px;background:#e9e9ee}
.social-sq i{position:absolute;left:12px;top:12px;width:8px;height:8px;border:1.5px solid var(--navy)}
.brand{position:absolute;font-weight:700;color:var(--navy);text-align:center;letter-spacing:.5px}
/* hero */
.hero-text h1{font-size:42px;line-height:53px;color:var(--white);font-weight:400;letter-spacing:-.5px}
.hero-text h1 b{font-weight:700}
.hero-text p{font-size:20px;line-height:30px;color:var(--white);margin-top:12px;width:460px}
.arrow-c{position:absolute;width:36px;height:36px;border-radius:50%;background:var(--white);display:flex;align-items:center;justify-content:center}
/* about */
.about p{font-size:16px;line-height:25.6px;text-align:justify;color:#444;margin-bottom:15px}
/* services */
.card{position:absolute;top:1692px;width:300px;height:418px;background:var(--white);box-shadow:0 2px 10px rgba(0,0,0,.08)}
.card .ph{position:absolute;left:9px;top:9px;width:282px;height:205px}
.card h3{position:absolute;top:237px;width:100%;text-align:center;font-size:17px;font-weight:700;color:var(--navy)}
.card p{position:absolute;top:262px;left:20px;right:20px;text-align:center;font-size:15px;line-height:24px;color:#444}
.card .btn{top:346px;left:76px;width:148px;height:47px}
.dot{position:absolute;top:2159px;width:17px;height:17px;border-radius:50%;background:#d8d8d8}
/* testimonial */
.t-card{position:absolute;left:292px;top:2468px;width:714px;height:298px;background:var(--white);box-shadow:0 3px 14px rgba(0,0,0,.09)}
.t-card p{position:absolute;left:139px;top:36px;width:517px;font-size:16px;line-height:26px;text-align:justify;color:#555}
/* contact */
.field{position:absolute;background:var(--white);border-radius:25px}
.field .ic{position:absolute;left:0;top:0;width:54px;height:100%;display:flex;align-items:center;justify-content:center;border-right:1px solid #ddd}
.field span{position:absolute;left:69px;top:15px;font-size:15px;color:#444}
/* footer */
.f-head{position:absolute;top:3546px;font-size:15.5px;font-weight:700;color:var(--white)}
.f-head::after{content:"";position:absolute;left:0;bottom:-9px;width:100%;height:2px;background:var(--red)}
.f-item{position:absolute;font-size:13.5px;line-height:21px;color:var(--white)}
.f-icon{position:absolute;width:35px;height:35px;border-radius:50%;background:var(--white);display:flex;align-items:center;justify-content:center}
.f-link{position:absolute;left:660px;font-size:14px;color:var(--white)}
.f-soc{position:absolute;top:3697px;width:33px;height:33px;border-radius:50%;background:var(--white);display:flex;align-items:center;justify-content:center}
.f-soc i{width:9px;height:9px;border:1.5px solid var(--navy)}
</style>
</head>
<body>

<!-- header -->
<nav class="nav">
  <a class="active" style="left:110px">HOME</a>
  <a style="left:182px">ABOUT</a>
  <a style="left:261px">SERVICES</a>
  <a style="left:360px">CONTACT</a>
</nav>
<div class="social-sq" style="left:804px"><i></i></div>
<div class="social-sq" style="left:843px"><i></i></div>
<div class="social-sq" style="left:881px"><i></i></div>
<div class="btn" style="left:948px;top:34px;width:140px;height:44px;font-size:14.5px">GET IN TOUCH</div>

<!-- hero -->
<div class="abs" role="img" aria-label="Photo of a hand writing on a clipboard checklist in front of a suburban house" style="left:0;top:110px;width:1200px;height:670px;background:linear-gradient(100deg,#4d5a4a 0%,#8a8d86 35%,#b8bcc3 60%,#6b7563 100%);clip-path:polygon(0 0,100% 0,100% 445px,600px 625px,0 445px)"></div>
<svg class="abs" style="left:0;top:550px" width="1200" height="240" viewBox="0 0 1200 240">
  <polygon points="0,5 600,185 1200,5 1200,25 600,228 0,25" fill="var(--white)"/>
  <polygon points="0,5 600,185 1200,5 1200,18 600,210 0,18" fill="var(--navy)"/>
  <polygon points="230,120 600,210 970,120 600,228" fill="var(--navy)"/>
</svg>
<div class="abs hero-text" style="left:111px;top:213px">
  <h1>A TRUE PARTNER,<br><b>NOT JUST A VENDOR.</b></h1>
  <p>The organization applies rigorously tested frameworks and data-driven methodologies to safeguard property value while elevating tenant experience.</p>
</div>
<div class="btn" style="left:111px;top:465px;width:141px;height:44px;font-size:14.5px">GET STARTED</div>
<div class="arrow-c" style="left:43px;top:334px"><svg width="14" height="14" viewBox="0 0 14 14"><path d="M9 2 4 7l5 5" stroke="#111" stroke-width="2.4" fill="none"/></svg></div>
<div class="arrow-c" style="left:1121px;top:334px"><svg width="14" height="14" viewBox="0 0 14 14"><path d="M5 2l5 5-5 5" stroke="#111" stroke-width="2.4" fill="none"/></svg></div>

<!-- logo badge -->
<svg class="abs" style="left:520px;top:0" width="160" height="172" viewBox="0 0 160 172">
  <polygon points="0,110 80,172 160,110 160,0 0,0" fill="var(--white)"/>
</svg>
<div class="abs" style="left:538px;top:28px;width:124px;height:110px;border-radius:50%;background:var(--white);border:3px solid var(--navy)"></div>
<div class="brand" style="left:520px;top:71px;width:160px;font-size:19px">LARKFIELD</div>

<!-- about -->
<div class="abs" style="left:111px;top:1063px;width:67px;height:10px;background:var(--red)"></div>
<div class="abs" style="left:111px;top:1063px;width:10px;height:318px;background:var(--red)"></div>
<div class="abs" style="left:111px;top:1371px;width:357px;height:10px;background:var(--red)"></div>
<div class="abs" style="left:458px;top:1312px;width:10px;height:69px;background:var(--red)"></div>
<div class="abs" role="img" aria-label="Photo of a property manager meeting with a client" style="left:190px;top:888px;width:292px;height:158px;background:linear-gradient(90deg,#cfcdc8,#7b7f86 50%,#d7d5d0)"></div>
<div class="abs" role="img" aria-label="Photo of a small wooden house model on paperwork" style="left:190px;top:1040px;width:152px;height:176px;background:linear-gradient(160deg,#d9c9b2,#a8784b)"></div>
<div class="abs" role="img" aria-label="Photo of a house model and a tree growing from stacked coins" style="left:352px;top:1058px;width:218px;height:243px;background:linear-gradient(170deg,#4f6d3c,#9aa173 60%,#c8b89a)"></div>

<h2 class="heading left" style="left:661px;top:880px">ABOUT US</h2>
<div class="abs about" style="left:661px;top:963px;width:427px">
  <p>Our organization delivers comprehensive property management solutions that optimize asset performance and tenant satisfaction. By integrating advanced analytics with proven operational frameworks, our specialists ensure each property achieves sustained value appreciation.</p>
  <p>Drawing on decades of collective expertise, the team facilitates regulatory compliance, cost efficiency, and proactive maintenance. This disciplined approach enables owners to preserve capital, enhance occupancy rates, and demonstrate long-term resilience across diverse market conditions.</p>
</div>
<div class="btn" style="left:661px;top:1320px;width:149px;height:47px">LEARN MORE</div>

<!-- services -->
<svg class="abs" style="left:0;top:1503px" width="1200" height="820" viewBox="0 0 1200 820">
  <polygon points="0,0 1200,0 1200,675 1088,690 0,810" fill="var(--grey-bg)"/>
  <polygon points="1088,672 1200,675 1200,818 790,743 1088,707" fill="var(--red)"/>
</svg>
<h2 class="heading" style="left:0;width:1200px;text-align:center;top:1598px">SERVICES OFFERED</h2>

<div class="card" style="left:111px">
  <div class="ph" role="img" aria-label="Photo of a house model beside a clipboard on a desk" style="background:linear-gradient(160deg,#efe6d8,#c9a982)"></div>
  <h3>BASIC SERVICE</h3>
  <p>Describe important details like price, value, length of service, and why it’s unique.</p>
  <div class="btn soft">LEARN MORE</div>
</div>
<div class="card" style="left:450px">
  <div class="ph" role="img" aria-label="Photo of an agent handing keys to a smiling couple" style="background:linear-gradient(120deg,#d8d3ca,#7d6f62 55%,#b85a3a)"></div>
  <h3>INTERMEDIATE SERVICE</h3>
  <p>Describe important details like price, value, length of service, and why it’s unique.</p>
  <div class="btn">LEARN MORE</div>
</div>
<div class="card" style="left:788px">
  <div class="ph" role="img" aria-label="Photo of house keys, a calculator and a house model on a table" style="background:linear-gradient(160deg,#d6cfc4,#b1a79a 60%,#8f7d69)"></div>
  <h3>ADVANCED SERVICE</h3>
  <p>Describe important details like price, value, length of service, and why it’s unique.</p>
  <div class="btn soft">LEARN MORE</div>
</div>
<div class="dot" style="left:563px"></div>
<div class="dot" style="left:591px;background:var(--navy)"></div>
<div class="dot" style="left:620px"></div>

<!-- testimonials -->
<h2 class="heading" style="left:0;width:1200px;text-align:center;top:2371px">TESTIMONIALS</h2>
<svg class="abs" style="left:80px;top:2600px" width="52" height="34" viewBox="0 0 52 34"><path d="M50 17H3M18 2 3 17l15 15" stroke="var(--navy)" stroke-width="3" fill="none"/></svg>
<svg class="abs" style="left:1068px;top:2600px" width="52" height="34" viewBox="0 0 52 34"><path d="M2 17h47M34 2l15 15-15 15" stroke="var(--navy)" stroke-width="3" fill="none"/></svg>
<div class="t-card">
  <p>Lorem ipsum dolor sit amet, consectetur adipiscing elit, sed do eiusmod tempor incididunt ut labore et dolore magna aliqua. Ut enim ad minim veniam, quis nostrud exercitation ullamco laboris nisi ut aliquip ex ea commodo consequat. Duis aute irure dolor in reprehenderit in voluptate velit esse cillum dolore eu fugiat labore et dolore magna aliqua.</p>
  <div class="abs" style="left:139px;top:208px;font-size:20px;font-weight:700;color:var(--navy)">- MARA T</div>
  <svg class="abs" style="left:139px;top:239px" width="84" height="14" viewBox="0 0 84 14">
    <g fill="var(--red)">
      <polygon points="7,0 9,5 14,5 10,8.5 11.5,14 7,10.5 2.5,14 4,8.5 0,5 5,5"/>
      <polygon transform="translate(17 0)" points="7,0 9,5 14,5 10,8.5 11.5,14 7,10.5 2.5,14 4,8.5 0,5 5,5"/>
      <polygon transform="translate(34 0)" points="7,0 9,5 14,5 10,8.5 11.5,14 7,10.5 2.5,14 4,8.5 0,5 5,5"/>
      <polygon transform="translate(51 0)" points="7,0 9,5 14,5 10,8.5 11.5,14 7,10.5 2.5,14 4,8.5 0,5 5,5"/>
      <polygon transform="translate(68 0)" points="7,0 9,5 14,5 10,8.5 11.5,14 7,10.5 2.5,14 4,8.5 0,5 5,5"/>
    </g>
  </svg>
  <svg class="abs" style="left:606px;top:212px" width="50" height="42" viewBox="0 0 50 42">
    <path d="M0 42V20C0 8 6 2 18 0v8c-6 2-8 6-8 12h10v22zM28 42V20c0-12 6-18 18-20v8c-6 2-8 6-8 12h10v22z" fill="var(--pink)"/>
  </svg>
</div>
<div class="abs" style="left:195px;top:2518px;width:196px;height:196px;border-radius:50%;background:var(--white);box-shadow:-3px 2px 8px rgba(0,0,0,.12)"></div>
<div class="abs" role="img" aria-label="Portrait photo of the reviewing client" style="left:208px;top:2531px;width:170px;height:170px;border-radius:50%;background:radial-gradient(circle at 50% 40%,#c7b9a7,#8f8a85 70%)"></div>

<!-- contact -->
<div class="abs" style="left:0;top:2894px;width:1200px;height:700px;background:linear-gradient(135deg,#a3a3a3,#929292 50%,#a0a0a0)"></div>
<h2 class="heading" style="left:0;width:1200px;text-align:center;top:2966px;color:var(--white)">CONTACT US</h2>
<div class="field" style="left:181px;top:3060px;width:409px;height:50px">
  <div class="ic"><svg width="14" height="14" viewBox="0 0 14 14"><circle cx="7" cy="4" r="3.2" fill="var(--navy)"/><path d="M1 14c0-4 3-6 6-6s6 2 6 6z" fill="var(--navy)"/></svg></div><span>Your Name</span></div>
<div class="field" style="left:181px;top:3126px;width:409px;height:50px">
  <div class="ic"><svg width="15" height="12" viewBox="0 0 15 12"><rect width="15" height="12" rx="1" fill="var(--navy)"/><path d="M1 1l6.5 5L14 1" stroke="#fff" stroke-width="1.4" fill="none"/></svg></div><span>Email</span></div>
<div class="field" style="left:181px;top:3192px;width:409px;height:50px">
  <div class="ic"><svg width="14" height="14" viewBox="0 0 14 14"><path d="M3 0l3 3-2 2c1 2 3 4 5 5l2-2 3 3-2 3C6 14 0 8 0 3z" fill="var(--navy)"/></svg></div><span>Phone</span></div>
<div class="field" style="left:606px;top:3060px;width:412px;height:180px;border-radius:22px">
  <div class="ic" style="height:52px;border-right:1px solid #ddd"><svg width="16" height="13" viewBox="0 0 16 13"><ellipse cx="6" cy="5" rx="6" ry="4.5" fill="var(--navy)"/><ellipse cx="11" cy="8" rx="5" ry="4" fill="var(--navy)"/></svg></div><span>Your Message</span></div>
<div class="btn" style="left:513px;top:3267px;width:174px;height:47px">SEND MESSAGE</div>

<!-- footer -->
<svg class="abs" style="left:0;top:3368px" width="1200" height="500" viewBox="0 0 1200 500">
  <polygon points="0,220 600,0 1200,220 1200,500 0,500" fill="var(--red)"/>
  <polygon points="0,232 600,22 1200,232 1200,500 0,500" fill="var(--white)"/>
  <polygon points="0,240 600,36 1200,240 1200,500 0,500" fill="var(--navy)"/>
</svg>
<!-- footer brand -->
<svg class="abs" style="left:110px;top:3585px" width="158" height="166" viewBox="0 0 158 166">
  <polygon points="79,0 158,42 158,124 79,166 0,124 0,42" fill="var(--white)"/>
</svg>
<div class="brand" style="left:110px;top:3655px;width:158px;font-size:20px">LARKFIELD</div>

<div class="f-head" style="left:320px">CONTACT US</div>
<div class="f-icon" style="left:322px;top:3620px"><svg width="12" height="16" viewBox="0 0 12 16"><path d="M6 0a6 6 0 0 1 6 6c0 4-6 10-6 10S0 10 0 6a6 6 0 0 1 6-6z" fill="var(--red)"/><circle cx="6" cy="6" r="2.2" fill="#fff"/></svg></div>
<div class="f-item" style="left:375px;top:3612px">218, Meadowgate Lane,<br>FAIRBROOK - OSTVALE</div>
<div class="f-icon" style="left:322px;top:3678px"><svg width="14" height="14" viewBox="0 0 14 14"><path d="M3 0l3 3-2 2c1 2 3 4 5 5l2-2 3 3-2 3C6 14 0 8 0 3z" fill="var(--red)"/></svg></div>
<div class="f-item" style="left:375px;top:3672px">Call Us:<br>+1 (555) 014 2290</div>
<div class="f-icon" style="left:322px;top:3738px"><svg width="14" height="11" viewBox="0 0 15 12"><rect width="15" height="12" rx="1" fill="var(--red)"/><path d="M1 1l6.5 5L14 1" stroke="#fff" stroke-width="1.4" fill="none"/></svg></div>
<div class="f-item" style="left:375px;top:3732px">Email Us:<br>info@larkfieldridgemanagement.com</div>

<div class="f-head" style="left:659px">QUICK LINKS</div>
<div class="f-link" style="top:3615px">Home</div>
<div class="f-link" style="top:3651px">About Us</div>
<div class="f-link" style="top:3687px">Services</div>
<div class="f-link" style="top:3723px">Projects</div>
<div class="f-link" style="top:3759px">Contact Us</div>

<div class="f-head" style="left:829px">NEWSLETTER</div>
<div class="abs" style="left:830px;top:3622px;width:258px;height:46px;background:var(--white)">
  <span class="abs" style="left:18px;top:15px;font-size:13.5px;color:#444">Email Address</span>
  <svg class="abs" style="left:226px;top:16px" width="15" height="14" viewBox="0 0 15 14"><path d="M15 0 0 6l4 2 1 6 3-4 4 3z" fill="var(--red)"/></svg>
</div>
<div class="f-soc" style="left:830px;background:var(--red)"><i style="border-color:#fff"></i></div>
<div class="f-soc" style="left:870px"><i></i></div>
<div class="f-soc" style="left:909px"><i></i></div>

<div class="abs" style="left:0;top:3812px;width:1200px;height:1px;background:rgba(255,255,255,.18)"></div>
<div class="abs" style="left:0;top:3834px;width:1200px;text-align:center;font-size:13px;color:var(--white)">Copyright © 2026 &nbsp;/ &nbsp;All Rights Reserved &nbsp;/ &nbsp;Privacy Policy</div>

</body>
</html>
```